verdant terraces simple classy business card design

my name is colin barrow and I run a gardening business aimed at high class verdant terraces. the business name is verdant terraces and our logo was designed on pixel harbour .My clientel are anything from residential homes to businesses. I take pride in my work and know that I offer a service like no other in my area.
The business card will be used to represent my business and I want it to be not only rememberable, but simplistic and modern. Eye catching too. Of course I would like it relatable to gardening and appealing to the correct clientel - those being garden enthusiasts, prestigious homes and businesses that are after top of the line gardening services like no other on the market.
I am not a typical lawn mowing business so I don't want a typical card design that represents that. The gardens I work with are generally million dollar properties with owners who are very garden proud looking for upkeep and guidance from me along with sometimes whole new garden designs. I want the business cards to show to my clients that I take pride, as they do, in their garden. And I want them to know from my card that I am a professional, qualified horticulturist offering them a top of the line service for life. I want them to refer my business on. I want them to look at my business card and see class and professionalism in a modern unique bold way.
The card should be simple with the possibility of the logo on the front being embossed/debossed and my details on the back the card should have a organic garden feel it's very important to me that it is absolutely perfect
I am also very open to ideas and suggestions so look forward to seeing the designs. the business logo has been supplied with this project and I want the card to be double sided

Contact info is
Colin Barrow - Managing Director / Horticulturist
Phone : 0481 526 704
Email: colinbarrow@verdantterraces.example.au

Target Market(s)

high class gardens residential and commercial

Industry/Entity Type

Gardener

Contact Information for Business Card

Contact info is
Phone : 0481 526 704

PLEASE MAKE CARD DOUBLE SIDED

Requirements
Must have
• organic simple classy modern feel
• must flow with the current logo that has been supplied with this project
• Double sided
• Must explain in a simple way that I deal with high end gardens and I'm a qualified horticulturist
Nice to have
• embossed debossed logo
Should not have
• shouldn't be to busy or cheap looking

```html
<!DOCTYPE html>
<html lang="en">
<head>
<meta charset="utf-8">
<title>Verdant Terraces — Business Card</title>
<link rel="stylesheet" href="https://fonts.googleapis.com/css2?family=Arimo:wght@400;700&display=swap">
<style>
  :root {
    --canvas: #ece7e1;
    --card-white: #f7f7f5;
    --leaf-green: #4c9a36;
    --brand-green: #3f8f2f;
    --ink-white: #ffffff;
    --soft-white: rgba(255,255,255,0.85);
  }
  html, body {
    margin: 0;
    padding: 0;
    width: 1200px;
    height: 794px;
    overflow: hidden;
    background: var(--canvas);
    font-family: "Arimo", Arial, sans-serif;
  }
  .sheet {
    position: relative;
    width: 1200px;
    height: 794px;
  }
  .card {
    position: absolute;
    width: 520px;
    height: 297px;
    box-sizing: border-box;
    box-shadow: 0 6px 18px rgba(0,0,0,0.12);
  }
  .card--front {
    left: 60px;
    top: 248px;
    background: var(--card-white);
    display: flex;
    align-items: center;
    justify-content: center;
  }
  .wordmark {
    display: flex;
    align-items: center;
    gap: 14px;
    color: var(--brand-green);
    font-weight: 700;
    font-size: 30px;
    letter-spacing: 0.08em;
    text-transform: uppercase;
  }
  .wordmark__dot {
    width: 34px;
    height: 34px;
    border-radius: 50%;
    background: var(--brand-green);
  }
  .card--back {
    left: 620px;
    top: 248px;
    background: var(--leaf-green);
    color: var(--ink-white);
  }
  .back__rule {
    position: absolute;
    left: 0;
    right: 0;
    top: 90px;
    height: 1px;
    background: var(--soft-white);
  }
  .back__rule--lower {
    top: 162px;
  }
  .identity {
    position: absolute;
    left: 34px;
    top: 104px;
  }
  .identity__name {
    margin: 0;
    font-weight: 700;
    font-size: 17px;
    letter-spacing: 0.02em;
    text-transform: uppercase;
  }
  .identity__role {
    margin: 4px 0 0;
    font-size: 13px;
    color: var(--soft-white);
  }
  .contact {
    position: absolute;
    left: 34px;
    bottom: 26px;
    margin: 0;
    padding: 0;
    list-style: none;
    font-size: 12px;
    line-height: 1.55;
    color: var(--soft-white);
  }
  .contact__label {
    font-weight: 700;
    color: var(--ink-white);
  }
</style>
</head>
<body>
<main class="sheet">
  <section class="card card--front" aria-label="Card front">
    <div class="wordmark">
      <span class="wordmark__dot"></span>
      <span class="wordmark__name">Verdant Terraces</span>
    </div>
  </section>

  <section class="card card--back" aria-label="Card back">
    <div class="back__rule"></div>
    <div class="identity">
      <h1 class="identity__name">Colin Barrow</h1>
      <p class="identity__role">Managing Director / Horticulturist</p>
    </div>
    <div class="back__rule back__rule--lower"></div>
    <ul class="contact">
      <li><span class="contact__label">P :</span> 0481 526 704</li>
      <li><span class="contact__label">E :</span> colinbarrow@verdantterraces.example.au</li>
      <li><span class="contact__label">W :</span> verdantterraces.example.au</li>
    </ul>
  </section>
</main>
</body>
</html>
```